New Business Card Design Project LORVANTI-Italy

we are LORVANTI-Italy
our company in the market for 3 years we are luxury cosmetic company and its about time for a facelift :)
i will like to have elegant luxurious and unique business card
that will give the person that get it a unique, luxurious and elegant impression
I'm VERY OPEN FOR NEW IDEAS , even duo i add a few files of things that i see on line and i like them

i add my logo as well
my website is LORVANTI.COM
(if you would like to see the main style that we have)

Target Market(s)

adult that have money :)

Industry/Entity Type

Business

Contact Information for Business Card

Name - Dario Lorvanti
Position - CEO and CO Founder
address - 4817 E Halvern
telephone - 555-384-1926
email - dario@lorvanti.com
fax - 555-384-1926
website - LORVANTI.COM

Colors
000000
959595
fbee3e
ffffff

Requirements
Must have
• big logo in GOLD color
• elegant look
• impressive
Nice to have
• not must but maybe classy pattern background
• not must but maybe emblem
• maybe clear plastic business card
Should not have
• colors
• images

```html
<!DOCTYPE html>
<html lang="en">
<head>
<meta charset="utf-8">
<title>Lorvanti Italy – Business Card</title>
<link rel="stylesheet" href="https://fonts.googleapis.com/css2?family=Tinos:wght@400;700&family=Lato:wght@400&display=swap">
<style>
  :root {
    --gold: #d6b04c;
    --gold-light: #e6c866;
    --gold-deep: #b8922f;
    --black: #0b0b0b;
    --ink: #111111;
    --grey-ring: #4a4a4a;
    --grey-ring-dark: #2a2a2a;
    --white: #ffffff;
    --stage-top: #d4d4d4;
    --stage-bottom: #ffffff;
  }
  * { margin: 0; padding: 0; box-sizing: border-box; }
  html, body { width: 1200px; height: 900px; overflow: hidden; }
  body {
    position: relative;
    background: linear-gradient(to bottom, var(--stage-top) 0%, var(--stage-bottom) 100%);
    font-family: "Lato", sans-serif;
  }
  .card {
    position: absolute;
    top: 184px;
    height: 490px;
    border-radius: 12px;
    overflow: hidden;
  }
  .card-back { left: 299px; width: 301px; background: var(--gold); }
  .card-front { left: 645px; width: 305px; background: var(--black); }
  .card-art { position: absolute; inset: 0; display: block; }
  .card-text {
    position: absolute;
    left: 0; right: 0;
    text-align: center;
  }

  /* Back side: contact details */
  .holder-name {
    top: 172px;
    font-family: "Tinos", serif;
    font-weight: 700;
    font-size: 19px;
    letter-spacing: 0.5px;
    color: var(--gold-light);
  }
  .holder-role {
    top: 197px;
    font-size: 13px;
    color: var(--white);
  }
  .rule {
    position: absolute;
    left: 50%;
    width: 100px;
    height: 1px;
    margin-left: -50px;
    background: var(--gold);
  }
  .rule-top { top: 227px; }
  .rule-bottom { top: 334px; }
  .contact-icons {
    position: absolute;
    top: 243px;
    left: 0; right: 0;
    display: flex;
    justify-content: center;
    gap: 6px;
  }
  .contact-icons svg { width: 16px; height: 16px; display: block; }
  .contact-lines {
    top: 268px;
    font-size: 13px;
    line-height: 18px;
    color: var(--white);
  }
  .holder-address {
    top: 348px;
    font-size: 13px;
    color: var(--white);
  }

  /* Front side: brand */
  .brand-seal {
    position: absolute;
    top: 112px;
    left: 50%;
    width: 104px;
    height: 104px;
    margin-left: -52px;
    border: 3px solid var(--gold);
    border-radius: 50%;
  }
  .brand-name {
    top: 233px;
    font-family: "Tinos", serif;
    font-size: 46px;
    line-height: 56px;
    letter-spacing: 1px;
    color: var(--gold-light);
  }
  .brand-rule {
    position: absolute;
    top: 294px;
    left: 35px;
    width: 236px;
    height: 2px;
    background: var(--gold);
  }
  .brand-origin {
    top: 302px;
    font-family: "Tinos", serif;
    font-size: 18px;
    color: var(--gold-light);
  }
  .brand-web {
    top: 357px;
    font-family: "Tinos", serif;
    font-weight: 700;
    font-size: 15px;
    letter-spacing: 0.5px;
    color: var(--gold-light);
  }
</style>
</head>
<body>

<section class="card card-back" aria-label="Business card, contact side">
  <svg class="card-art" viewBox="0 0 301 490" aria-hidden="false">
    <defs>
      <linearGradient id="goldRing" x1="0" y1="0" x2="1" y2="1">
        <stop offset="0" stop-color="#e8cb68"/>
        <stop offset="0.5" stop-color="#d9b34a"/>
        <stop offset="1" stop-color="#c49b36"/>
      </linearGradient>
    </defs>
    <path role="img" aria-label="Woven gold lattice ring pattern"
          fill="url(#goldRing)" fill-rule="evenodd"
          d="M -71 256 a222 222 0 1 0 444 0 a222 222 0 1 0 -444 0 Z
             M -24 256 a175 175 0 1 0 350 0 a175 175 0 1 0 -350 0 Z"/>
    <circle cx="151" cy="256" r="175" fill="var(--ink)"/>
  </svg>

  <p class="card-text holder-name">DARIO LORVANTI</p>
  <p class="card-text holder-role">CEO and CO Founder</p>
  <span class="rule rule-top"></span>

  <div class="contact-icons">
    <svg viewBox="0 0 16 16" aria-label="Phone">
      <circle cx="8" cy="8" r="8" fill="var(--gold)"/>
      <path d="M4.5 6.5 q3.5 -3 7 0 l-1 1.2 h-1.2 v-0.9 h-2.6 v0.9 h-1.2 Z M5.5 8.5 h5 l0.6 3 h-6.2 Z" fill="var(--ink)"/>
    </svg>
    <svg viewBox="0 0 16 16" aria-label="Fax">
      <circle cx="8" cy="8" r="8" fill="var(--gold)"/>
      <rect x="5.5" y="3.8" width="5" height="3" fill="var(--ink)"/>
      <rect x="4.5" y="7.3" width="7" height="5" rx="0.6" fill="var(--ink)"/>
      <rect x="6" y="9" width="4" height="0.8" fill="var(--gold)"/>
    </svg>
    <svg viewBox="0 0 16 16" aria-label="Email">
      <circle cx="8" cy="8" r="8" fill="var(--gold)"/>
      <rect x="4" y="5.3" width="8" height="5.6" fill="var(--ink)"/>
      <path d="M4.3 5.6 L8 8.4 L11.7 5.6" fill="none" stroke="var(--gold)" stroke-width="0.8"/>
    </svg>
  </div>

  <p class="card-text contact-lines">555-384-1926<br>555-384-1926<br>dario@lorvanti.com</p>
  <span class="rule rule-bottom"></span>
  <p class="card-text holder-address">4817 E Halvern</p>
</section>

<section class="card card-front" aria-label="Business card, brand side">
  <svg class="card-art" viewBox="0 0 305 490">
    <defs>
      <radialGradient id="greyRing" cx="0.5" cy="0.5" r="0.5">
        <stop offset="0.78" stop-color="#2c2c2c"/>
        <stop offset="1" stop-color="#4c4c4c"/>
      </radialGradient>
    </defs>
    <path role="img" aria-label="Faint grey woven lattice ring pattern"
          fill="url(#greyRing)" fill-rule="evenodd"
          d="M -88 246 a240 240 0 1 0 480 0 a240 240 0 1 0 -480 0 Z
             M -36 246 a188 188 0 1 0 376 0 a188 188 0 1 0 -376 0 Z"/>
  </svg>

  <span class="brand-seal"></span>
  <p class="card-text brand-name">LORVANTI</p>
  <span class="brand-rule"></span>
  <p class="card-text brand-origin">ITALY</p>
  <p class="card-text brand-web">LORVANTI.COM</p>
</section>

</body>
</html>
```